RTavenor Business Cards & Letterhead

I have a logo but need a design for some new business cards. We are a Design-Build Firm that specializes in the design and construction of commercial projects.
the cards need to be professional. no cartoon stuff.
i would like to have the cards in AI format so I can update the card as needed. Logo is provided.
Our Address is: 4187 Marlowe Ct. Kessler, North Lindale 27614

```html
<!DOCTYPE html>
<html lang="en">
<head>
<meta charset="utf-8">
<title>RTavenor Business Card</title>
<link rel="stylesheet" href="https://fonts.googleapis.com/css2?family=Open+Sans:wght@400;600;700&display=swap">
<style>
  :root{
    --stage:#242424;
    --card-dark:#232327;
    --blue:#1676b8;
    --blue-deep:#0b3a63;
    --blue-mid:#125a92;
    --white:#f4f6f8;
  }
  html,body{margin:0;padding:0;overflow:hidden;}
  body{width:1200px;height:780px;background:var(--stage);font-family:"Open Sans",Arial,sans-serif;position:relative;}
  .card{position:absolute;top:90px;width:350px;height:600px;border-radius:26px;overflow:hidden;box-shadow:0 14px 30px rgba(0,0,0,.55);}
  .card-front{left:215px;background:radial-gradient(ellipse at 55% 50%,#1479be 0%,#0f5489 45%,var(--blue-deep) 100%);}
  .front-wordmark{position:absolute;left:50%;top:50%;transform:translate(-50%,-50%) rotate(90deg);font-size:58px;font-weight:700;letter-spacing:3px;color:#0e4e82;white-space:nowrap;}
  .card-back{left:635px;background:var(--card-dark);color:var(--white);text-align:center;}
  .brand{position:absolute;top:120px;left:0;right:0;display:flex;align-items:center;justify-content:center;gap:14px;}
  .brand-square{width:34px;height:34px;background:var(--blue);}
  .brand-name{font-size:36px;font-weight:700;color:var(--blue);}
  .person{position:absolute;top:318px;left:0;right:0;}
  .person-name{font-size:26px;font-weight:700;color:var(--blue);letter-spacing:1px;margin:0;}
  .person-title{font-size:15px;font-weight:600;margin:2px 0 0;}
  .dots{display:block;margin:0 auto;}
  .row-top{position:absolute;top:386px;left:25px;}
  .contact{position:absolute;top:410px;left:0;right:0;font-size:15px;line-height:23px;}
  .contact p{margin:0;}
  .row-mid{position:absolute;top:486px;left:25px;}
  .address{position:absolute;top:512px;left:0;right:0;font-size:15px;line-height:22px;}
  .address p{margin:0;}
</style>
</head>
<body>
  <section class="card card-front" aria-label="Card front">
    <div class="front-wordmark">RTAVENOR</div>
  </section>

  <section class="card card-back" aria-label="Card back">
    <div class="brand"><span class="brand-square"></span><span class="brand-name">RTavenor</span></div>

    <div class="person">
      <p class="person-name">DORIAN TAVENOR</p>
      <p class="person-title">Founder/President</p>
    </div>

    <svg class="dots row-top" width="300" height="22" viewBox="0 0 300 22" aria-hidden="true">
      <g fill="var(--blue-mid)">
        <circle cx="6" cy="11" r="2.5"/><circle cx="18" cy="11" r="3.5"/><circle cx="32" cy="11" r="4.5"/><circle cx="48" cy="11" r="5.5"/><circle cx="66" cy="11" r="6.5"/>
        <circle cx="234" cy="11" r="6.5"/><circle cx="252" cy="11" r="5.5"/><circle cx="268" cy="11" r="4.5"/><circle cx="282" cy="11" r="3.5"/><circle cx="294" cy="11" r="2.5"/>
      </g>
      <g fill="var(--blue)">
        <circle cx="114" cy="11" r="10"/><circle cx="150" cy="11" r="10"/><circle cx="186" cy="11" r="10"/>
      </g>
      <g fill="none" stroke="var(--white)" stroke-width="1.4">
        <path d="M110 7c0 5 3 8 8 8l1-2-2-2-1 1c-2-1-3-2-4-4l1-1-2-2z"/>
        <rect x="144" y="7" width="12" height="8"/><path d="M144 7l6 5 6-5"/>
        <circle cx="186" cy="11" r="5.5"/><path d="M180.5 11h11M186 5.5c-3 3-3 8 0 11M186 5.5c3 3 3 8 0 11"/>
      </g>
    </svg>

    <div class="contact">
      <p>(555) 014-8273</p>
      <p>www.rtavenor.com</p>
      <p>DT@RTavenor.com</p>
    </div>

    <svg class="dots row-mid" width="300" height="22" viewBox="0 0 300 22" aria-hidden="true">
      <g fill="var(--blue-mid)">
        <circle cx="6" cy="11" r="2.5"/><circle cx="18" cy="11" r="3.5"/><circle cx="32" cy="11" r="4.5"/><circle cx="48" cy="11" r="5.5"/><circle cx="66" cy="11" r="6.5"/><circle cx="86" cy="11" r="7.5"/>
        <circle cx="214" cy="11" r="7.5"/><circle cx="234" cy="11" r="6.5"/><circle cx="252" cy="11" r="5.5"/><circle cx="268" cy="11" r="4.5"/><circle cx="282" cy="11" r="3.5"/><circle cx="294" cy="11" r="2.5"/>
      </g>
      <circle cx="150" cy="11" r="10" fill="var(--blue)"/>
      <g fill="none" stroke="var(--white)" stroke-width="1.4">
        <path d="M150 17c-4-4-5-6-5-8a5 5 0 0 1 10 0c0 2-1 4-5 8z"/><circle cx="150" cy="9" r="1.6"/>
      </g>
    </svg>

    <div class="address">
      <p>4187 Marlowe Ct. Kessler,</p>
      <p>North Lindale 27614</p>
    </div>
  </section>
</body>
</html>
```